Wren Hollow Farm Postcard Design

I am looking for a new postcard design to mail out this season. We are a Farm business that does wholesale and retail and bulk seasoned firewood sales. we sell firewood from anything from bagged wood to tractor trailer loads of wood. We sell firewood in bulk bags. Pick up or delivery available there is no order to big or too small. I need my business name and phone number on the cards Wren Hollow Farm 615-302-4187 (call or text) I would like it to say we are the best priced guaranteed. I want something that is simple and straight forward but also really catches the eye when they see these in the mail box. I attached my logo and feel free to use photos of split firewood if you would like. id like my email on the card Wrenhollowfarm47@maplepost.net.

Target Market(s)

Firewood purchasers

Industry/Entity Type

agriculture

Requirements
Must have
• email phone number logo

```html
<!DOCTYPE html>
<html lang="en">
<head>
<meta charset="utf-8">
<title>Wren Hollow Farm Postcard</title>
<link href="https://fonts.googleapis.com/css2?family=Oswald:wght@500;600;700&family=Montserrat:wght@500;600;700&family=Arimo:wght@400;700&display=swap" rel="stylesheet">
<style>
  :root {
    --stage: #c8c8c8;
    --ink-black: #0b0b0b;
    --maroon: #7f1f1f;
    --maroon-text: #8b2321;
    --bark: #5e4532;
    --flame: #e0731f;
    --gold: #f39a1e;
    --white: #ffffff;
    --dark-text: #141414;
    --rule: #8a8a8a;
  }
  * { box-sizing: border-box; margin: 0; padding: 0; }
  html, body { width: 1200px; height: 1200px; overflow: hidden; }
  body { background: var(--stage); position: relative; font-family: "Montserrat", sans-serif; }

  .card { position: absolute; left: 216px; width: 776px; height: 518px; overflow: hidden; box-shadow: 0 2px 6px rgba(0,0,0,.25); }
  .card-front { top: 64px; background: var(--ink-black); }
  .card-back { top: 621px; background: var(--white); }
  .abs { position: absolute; }

  /* ---------- front ---------- */
  .wood-stack-photo { left: 0; top: 0; width: 300px; height: 305px; background: linear-gradient(160deg, #a0703f 0%, #7a4c2a 55%, #4e3019 100%); }
  .truck-photo { left: 280px; top: 70px; width: 465px; height: 260px; background: linear-gradient(180deg, #2a2a2a 0%, #7d1c1c 40%, #5a1212 70%, #9a9a9a 100%); border-radius: 10px 10px 4px 4px; }
  .tab-wholesale { left: 0; top: 0; width: 290px; height: 55px; background: var(--white); clip-path: polygon(0 0, 100% 0, 94% 100%, 0 100%); font-family: "Oswald", sans-serif; font-weight: 600; font-size: 31px; color: var(--maroon-text); line-height: 55px; padding-left: 14px; }
  .headline { left: 16px; top: 150px; font-family: "Oswald", sans-serif; font-weight: 600; color: var(--white); line-height: 1; text-shadow: 0 2px 6px rgba(0,0,0,.55); }
  .headline .line-small { display: block; font-size: 43px; }
  .headline .line-big { display: block; font-size: 64px; }
  .band-sales { left: 0; top: 264px; width: 172px; height: 40px; background: var(--maroon-text); clip-path: polygon(0 0, 88% 0, 100% 100%, 0 100%); color: var(--white); font-weight: 600; font-size: 27px; line-height: 40px; padding-left: 20px; }
  .brand-name { left: 560px; top: 24px; width: 205px; text-align: center; font-family: "Oswald", sans-serif; font-weight: 700; font-size: 36px; line-height: 1.05; color: var(--gold); }
  .offer-box { left: 15px; top: 307px; width: 746px; height: 134px; background: var(--bark); border: 3px solid var(--flame); }
  .offer-text { position: absolute; left: 0; top: 0; width: 530px; height: 100%; display: flex; flex-direction: column; justify-content: center; align-items: center; color: var(--white); font-weight: 600; font-size: 22.5px; line-height: 1.3; text-align: center; }
  .badge { display: block; }
  .badge-front { left: 548px; top: 303px; width: 192px; height: 142px; }
  .badge-back { left: 292px; top: 86px; width: 122px; height: 118px; }

  /* ---------- contact bar ---------- */
  .contact-bar { left: 0; top: 457px; width: 776px; height: 61px; background: var(--maroon); }
  .contact-bar .email-panel { position: absolute; left: 58px; top: 0; width: 412px; height: 61px; background: var(--white); clip-path: polygon(0 0, 100% 0, 94% 100%, 4% 100%); display: flex; align-items: center; padding-left: 28px; font-weight: 600; font-size: 18px; color: var(--dark-text); }
  .contact-bar .icon { position: absolute; top: 15px; width: 31px; height: 31px; }
  .contact-bar .icon-mail { left: 14px; }
  .contact-bar .icon-phone { left: 483px; }
  .contact-bar .phone-block { position: absolute; left: 527px; top: 4px; color: var(--white); font-weight: 700; line-height: 1; }
  .phone-block .label { display: block; font-size: 20px; letter-spacing: .3px; }
  .phone-block .number { display: block; font-size: 27px; margin-top: 3px; }

  /* ---------- back ---------- */
  .back-shapes { left: 0; top: 0; width: 776px; height: 457px; }
  .pickup-head { left: 20px; top: 18px; color: var(--white); }
  .pickup-head .title { font-weight: 700; font-size: 26px; line-height: 1.12; }
  .pickup-head .title u { text-decoration-thickness: 2px; text-underline-offset: 4px; }
  .pickup-head .sub { margin-top: 10px; font-weight: 500; font-size: 15.5px; line-height: 1.15; color: #f0dcdc; }
  .processor-photo { left: 20px; top: 152px; width: 322px; height: 293px; background: linear-gradient(180deg, #8fb3d6 0%, #6b8c5e 28%, #25402a 55%, #c9a235 80%, #8a6a45 100%); }
  .split-wood-photo { left: 300px; top: 318px; width: 178px; height: 128px; background: linear-gradient(150deg, #e2bf8e 0%, #b98a55 55%, #7b5431 100%); border-radius: 30px 8px 6px 40px; }
  .indicia { left: 637px; top: 32px; width: 122px; height: 90px; border: 1px solid var(--rule); font-family: "Arimo", sans-serif; font-weight: 700; font-size: 12.5px; line-height: 1.2; text-align: center; color: var(--dark-text); padding-top: 6px; }
  .indicia .big { font-size: 15px; }
  .indicia .thin { font-weight: 700; }
  .address-box { left: 516px; top: 169px; width: 187px; height: 66px; border: 1px solid var(--rule); font-family: "Arimo", sans-serif; font-size: 15px; line-height: 1.3; text-align: center; color: #222; display: flex; align-items: center; justify-content: center; }
</style>
</head>
<body>

<!-- FRONT -->
<section class="card card-front">
  <div class="abs wood-stack-photo" role="img" aria-label="Photo of a neatly stacked pile of split seasoned firewood"></div>
  <div class="abs truck-photo" role="img" aria-label="Photo of a red tractor trailer truck cab with chrome stacks"></div>

  <div class="abs tab-wholesale">WHOLESALE &amp; RETAIL</div>
  <h1 class="abs headline"><span class="line-small">BULK SEASONED</span><span class="line-big">FIREWOOD</span></h1>
  <div class="abs band-sales">SALES</div>

  <div class="abs brand-name">Wren Hollow<br>Farm</div>

  <div class="abs offer-box">
    <p class="offer-text">WE SELL FIREWOOD<br>FROM BAGGED WOOD TO TRACTOR<br>TRAILER LOADS OF WOOD</p>
  </div>

  <svg class="abs badge badge-front" viewBox="0 0 100 100" preserveAspectRatio="none" aria-label="Best price guaranteed">
    <defs>
      <linearGradient id="flameFront" x1="0" y1="0" x2="0" y2="1">
        <stop offset="0" stop-color="#f7b02a"/>
        <stop offset="1" stop-color="#e4471f"/>
      </linearGradient>
    </defs>
    <polygon fill="url(#flameFront)" points="100,50 92.2,58.4 96.2,69.2 85.7,73.9 85.4,85.4 73.9,85.7 69.2,96.2 58.4,92.2 50,100 41.6,92.2 30.8,96.2 26.1,85.7 14.6,85.4 14.3,73.9 3.8,69.2 7.8,58.4 0,50 7.8,41.6 3.8,30.8 14.3,26.1 14.6,14.6 26.1,14.3 30.8,3.8 41.6,7.8 50,0 58.4,7.8 69.2,3.8 73.9,14.3 85.4,14.6 85.7,26.1 96.2,30.8 92.2,41.6"/>
    <path d="M38 24 L47 34 L66 8" fill="none" stroke="#fff" stroke-width="5" stroke-linecap="round" stroke-linejoin="round"/>
    <text x="50" y="58" text-anchor="middle" font-family="Montserrat, sans-serif" font-weight="600" font-size="13" fill="#fff">BEST PRICE</text>
    <text x="50" y="74" text-anchor="middle" font-family="Montserrat, sans-serif" font-weight="600" font-size="13" fill="#fff">Guaranteed</text>
  </svg>

  <div class="abs contact-bar">
    <svg class="icon icon-mail" viewBox="0 0 32 32" aria-hidden="true">
      <circle cx="16" cy="16" r="15" fill="#e8641f" stroke="#fff" stroke-width="1.5"/>
      <rect x="8.5" y="10.5" width="15" height="11" rx="1" fill="#fff"/>
      <path d="M8.5 11 L16 17 L23.5 11" fill="none" stroke="#e8641f" stroke-width="1.6"/>
    </svg>
    <div class="email-panel">Wrenhollowfarm47@maplepost.net</div>
    <svg class="icon icon-phone" viewBox="0 0 32 32" aria-hidden="true">
      <circle cx="16" cy="16" r="15" fill="#e8641f" stroke="#fff" stroke-width="1.5"/>
      <path d="M11 8.5 L14 8.5 L15 13 L13 14.5 Q14.5 18 17.5 19 L19 17 L23.5 18 L23.5 21 Q22.5 23.5 19.5 23 Q10 20 9 11.5 Q9 9 11 8.5 Z" fill="#fff"/>
    </svg>
    <div class="phone-block"><span class="label">CALL OR TEXT</span><span class="number">615-302-4187</span></div>
  </div>
</section>

<!-- BACK -->
<section class="card card-back">
  <svg class="abs back-shapes" viewBox="0 0 776 457" aria-hidden="true">
    <polygon points="0,0 415,0 345,180 345,457 0,457" fill="var(--ink-black)"/>
    <polygon points="0,0 395,0 340,138 0,138" fill="var(--maroon)"/>
  </svg>

  <div class="abs pickup-head">
    <h2 class="title">PICK UP OR DELIVERY<br><u>AVAILABLE</u></h2>
    <p class="sub">THERE IS NO ORDER<br>TO BIG OR TOO SMALL</p>
  </div>

  <div class="abs processor-photo" role="img" aria-label="Photo of a green and yellow firewood processing machine in a wooded yard"></div>
  <div class="abs split-wood-photo" role="img" aria-label="Photo of a small pile of freshly split firewood pieces"></div>

  <svg class="abs badge badge-back" viewBox="0 0 100 100" preserveAspectRatio="none" aria-label="Best price guaranteed">
    <defs>
      <linearGradient id="flameBack" x1="0" y1="0" x2="0" y2="1">
        <stop offset="0" stop-color="#f7b02a"/>
        <stop offset="1" stop-color="#e4471f"/>
      </linearGradient>
    </defs>
    <polygon fill="url(#flameBack)" points="100,50 92.2,58.4 96.2,69.2 85.7,73.9 85.4,85.4 73.9,85.7 69.2,96.2 58.4,92.2 50,100 41.6,92.2 30.8,96.2 26.1,85.7 14.6,85.4 14.3,73.9 3.8,69.2 7.8,58.4 0,50 7.8,41.6 3.8,30.8 14.3,26.1 14.6,14.6 26.1,14.3 30.8,3.8 41.6,7.8 50,0 58.4,7.8 69.2,3.8 73.9,14.3 85.4,14.6 85.7,26.1 96.2,30.8 92.2,41.6"/>
    <text x="50" y="37" text-anchor="middle" font-family="Montserrat, sans-serif" font-weight="700" font-size="15" fill="#fff">BEST</text>
    <text x="50" y="55" text-anchor="middle" font-family="Montserrat, sans-serif" font-weight="700" font-size="15" fill="#fff">PRICE</text>
    <text x="50" y="68" text-anchor="middle" font-family="Montserrat, sans-serif" font-weight="700" font-size="8" fill="#fff">GUARANTEED</text>
  </svg>

  <div class="abs indicia">
    PRSRT STD<br>ECRWSS<br>U.S.POSTAGE<br><span class="big">PAID</span><br><span class="thin">EDDM Retail</span>
  </div>
  <div class="abs address-box">Local Postal<br>Customer</div>

  <div class="abs contact-bar">
    <svg class="icon icon-mail" viewBox="0 0 32 32" aria-hidden="true">
      <circle cx="16" cy="16" r="15" fill="#e8641f" stroke="#fff" stroke-width="1.5"/>
      <rect x="8.5" y="10.5" width="15" height="11" rx="1" fill="#fff"/>
      <path d="M8.5 11 L16 17 L23.5 11" fill="none" stroke="#e8641f" stroke-width="1.6"/>
    </svg>
    <div class="email-panel">Wrenhollowfarm47@maplepost.net</div>
    <svg class="icon icon-phone" viewBox="0 0 32 32" aria-hidden="true">
      <circle cx="16" cy="16" r="15" fill="#e8641f" stroke="#fff" stroke-width="1.5"/>
      <path d="M11 8.5 L14 8.5 L15 13 L13 14.5 Q14.5 18 17.5 19 L19 17 L23.5 18 L23.5 21 Q22.5 23.5 19.5 23 Q10 20 9 11.5 Q9 9 11 8.5 Z" fill="#fff"/>
    </svg>
    <div class="phone-block"><span class="label">CALL OR TEXT</span><span class="number">615-302-4187</span></div>
  </div>
</section>

</body>
</html>
```